8 behaviours infographic

We are a portfolio of approx. 200 resources in technology within a financial services enterprise (5000-6000 employees).
Our portfolio name is Tidewater and Copperline Harbor Group.
Our leadership team has collectively defined a set of 8 behaviours that represent how we should behave and interact amongst ourselves.
We need an infographic that can bring these behaviours to life and be displayed around the workplace on large posters where teams work (the words for the behaviours should also be incorporated into the infographic).
We have also included our team's logo, which needs to be incorporated into the infographic.
The 8 behaviours are:
- Listen & show you care
- Support Each Other
- Be Accountable
- Communicate openly
- Collaborate and leverage the collective strength of the group
- Influence the agenda
- Proactive deliberate and team focussed
- Celebrate success & have fun

```html
<!DOCTYPE html>
<html lang="en">
<head>
<meta charset="utf-8">
<title>Eight Behaviours – Tidewater and Copperline Harbor Group</title>
<link rel="stylesheet" href="https://fonts.googleapis.com/css2?family=Comic+Neue:wght@400;700&display=swap">
<style>
  :root {
    --blue: #0a74bb;
    --ink: #151a33;
    --ring: #0a74bb;
    --bg-center: #ffffff;
    --bg-edge: #e8ecf1;
    --pill-light: #f2f3f5;
    --pill-dark: #d2d4d8;
    --icon: #ffffff;
  }
  html, body {
    margin: 0;
    padding: 0;
    width: 1200px;
    height: 1001px;
    overflow: hidden;
  }
  .poster {
    position: relative;
    width: 1200px;
    height: 1001px;
    background: radial-gradient(ellipse at 50% 50%, var(--bg-center) 0%, #f5f7f9 45%, var(--bg-edge) 100%);
    font-family: "Comic Neue", "Comic Sans MS", cursive;
  }
  .poster svg { position: absolute; inset: 0; }
  .connector { fill: none; stroke: var(--blue); stroke-width: 2.5; }
  .hub-dot { fill: var(--blue); }
  .badge-ring { fill: #ffffff; stroke: var(--ring); stroke-width: 2.5; }
  .badge-core { fill: var(--blue); }
  .icon { fill: none; stroke: var(--icon); stroke-width: 2.6; stroke-linecap: round; stroke-linejoin: round; }
  .behaviour-label {
    font-family: "Comic Neue", "Comic Sans MS", cursive;
    font-size: 22px;
    font-weight: 700;
    fill: var(--ink);
    text-anchor: middle;
    letter-spacing: 0.3px;
  }
  .pill-frame { fill: none; stroke: var(--blue); stroke-width: 2.5; }
  .pill-accent { fill: none; stroke: var(--blue); stroke-width: 7; stroke-linecap: butt; }
  .team-name {
    font-family: "Comic Neue", "Comic Sans MS", cursive;
    font-size: 38px;
    font-weight: 700;
    fill: var(--ink);
    text-anchor: middle;
  }
</style>
</head>
<body>
<main class="poster">
  <svg width="1200" height="1001" viewBox="0 0 1200 1001" xmlns="http://www.w3.org/2000/svg">
    <defs>
      <linearGradient id="pillFill" x1="0" y1="0" x2="0" y2="1">
        <stop offset="0" stop-color="var(--pill-dark)"/>
        <stop offset="0.5" stop-color="var(--pill-light)"/>
        <stop offset="1" stop-color="var(--pill-dark)"/>
      </linearGradient>
    </defs>

    <!-- connectors top -->
    <g class="connectors-top">
      <path class="connector" d="M232 298 V355 H550 V376"/>
      <path class="connector" d="M481 298 V325 H587 V376"/>
      <path class="connector" d="M729 298 V325 H624 V376"/>
      <path class="connector" d="M978 298 V355 H660 V376"/>
      <circle class="hub-dot" cx="550" cy="376" r="11"/>
      <circle class="hub-dot" cx="587" cy="376" r="11"/>
      <circle class="hub-dot" cx="624" cy="376" r="11"/>
      <circle class="hub-dot" cx="660" cy="376" r="11"/>
    </g>

    <!-- connectors bottom -->
    <g class="connectors-bottom">
      <path class="connector" d="M550 634 V655 H232 V710"/>
      <path class="connector" d="M587 634 V685 H481 V710"/>
      <path class="connector" d="M624 634 V685 H729 V710"/>
      <path class="connector" d="M660 634 V655 H978 V710"/>
      <circle class="hub-dot" cx="550" cy="634" r="11"/>
      <circle class="hub-dot" cx="587" cy="634" r="11"/>
      <circle class="hub-dot" cx="624" cy="634" r="11"/>
      <circle class="hub-dot" cx="660" cy="634" r="11"/>
    </g>

    <!-- central name pill -->
    <g class="team-pill">
      <rect class="pill-frame" x="300" y="403" width="612" height="201" rx="100.5"/>
      <path class="pill-accent" d="M301 497 A96 96 0 0 1 400 406 H811 A97 97 0 0 1 811 601 H820"/>
      <rect x="330" y="433" width="555" height="144" rx="72" fill="url(#pillFill)"/>
      <text class="team-name" x="607" y="495">Tidewater and Copperline</text>
      <text class="team-name" x="607" y="540">Harbor Group</text>
    </g>

    <!-- badge: proactive -->
    <g class="badge badge-proactive">
      <circle class="badge-ring" cx="232" cy="211" r="87"/>
      <circle class="badge-core" cx="232" cy="211" r="73"/>
      <g class="icon">
        <circle cx="232" cy="186" r="13"/>
        <path d="M208 228 V220 A24 24 0 0 1 256 220 V228"/>
        <circle cx="197" cy="196" r="10"/>
        <path d="M177 226 V220 A18 18 0 0 1 205 206"/>
        <circle cx="267" cy="196" r="10"/>
        <path d="M287 226 V220 A18 18 0 0 0 259 206"/>
      </g>
    </g>

    <!-- badge: influence -->
    <g class="badge badge-influence">
      <circle class="badge-ring" cx="481" cy="211" r="87"/>
      <circle class="badge-core" cx="481" cy="211" r="73"/>
      <g class="icon">
        <rect x="440" y="172" width="82" height="80" rx="5"/>
        <line x1="440" y1="192" x2="522" y2="192"/>
        <line x1="460" y1="164" x2="460" y2="180"/>
        <line x1="502" y1="164" x2="502" y2="180"/>
        <path d="M470 208 V224 A12 12 0 0 0 494 224 V208"/>
        <path d="M480 208 V224 A2 2 0 0 0 484 224 V208"/>
      </g>
    </g>

    <!-- badge: collaborate -->
    <g class="badge badge-collaborate">
      <circle class="badge-ring" cx="729" cy="211" r="87"/>
      <circle class="badge-core" cx="729" cy="211" r="73"/>
      <g class="icon">
        <path d="M678 196 L694 186 L720 198 L738 190"/>
        <path d="M780 196 L764 186 L742 190 L720 206 A6 6 0 0 0 730 214 L746 204"/>
        <path d="M692 206 L708 230 A6 6 0 0 0 718 236 L740 240 A6 6 0 0 0 748 232"/>
        <path d="M746 204 L764 218 A6 6 0 0 1 756 228 L748 232"/>
        <path d="M700 220 L708 212 M708 228 L716 220 M716 234 L724 226"/>
        <path d="M670 200 L686 224 M788 200 L772 224"/>
      </g>
    </g>

    <!-- badge: support -->
    <g class="badge badge-support">
      <circle class="badge-ring" cx="978" cy="211" r="87"/>
      <circle class="badge-core" cx="978" cy="211" r="73"/>
      <g class="icon">
        <path d="M944 210 V200 A34 34 0 0 1 1012 200 V210"/>
        <rect x="930" y="198" width="16" height="30" rx="6"/>
        <rect x="1010" y="198" width="16" height="30" rx="6"/>
        <path d="M1012 228 V234 A14 14 0 0 1 998 248 H984"/>
        <rect x="968" y="242" width="16" height="10" rx="4"/>
      </g>
    </g>

    <!-- badge: listen -->
    <g class="badge badge-listen">
      <circle class="badge-ring" cx="232" cy="797" r="87"/>
      <circle class="badge-core" cx="232" cy="797" r="73"/>
      <g class="icon">
        <circle cx="244" cy="776" r="28"/>
        <path d="M222 762 Q232 768 230 778 Q240 782 238 792 M256 752 Q250 764 262 770 Q270 772 270 782"/>
        <path d="M180 804 H190 L208 810 H230 A5 5 0 0 1 230 820 H212 M230 820 L258 812 A6 6 0 0 1 266 822 L234 838 H200 L190 834 H180"/>
        <rect x="174" y="800" width="8" height="38" rx="2"/>
      </g>
    </g>

    <!-- badge: communicate -->
    <g class="badge badge-communicate">
      <circle class="badge-ring" cx="481" cy="797" r="87"/>
      <circle class="badge-core" cx="481" cy="797" r="73"/>
      <g class="icon">
        <path d="M470 750 A36 26 0 1 1 462 800 L446 812 L450 796 A36 26 0 0 1 470 750 Z"/>
        <circle cx="458" cy="776" r="2" fill="#fff"/>
        <circle cx="471" cy="776" r="2" fill="#fff"/>
        <circle cx="484" cy="776" r="2" fill="#fff"/>
        <path d="M510 786 A26 20 0 1 1 486 826 L470 832 L476 818"/>
      </g>
    </g>

    <!-- badge: celebrate -->
    <g class="badge badge-celebrate">
      <circle class="badge-ring" cx="729" cy="797" r="87"/>
      <circle class="badge-core" cx="729" cy="797" r="73"/>
      <g class="icon">
        <path d="M690 770 L714 776 L706 808 A12 12 0 0 1 686 802 Z"/>
        <path d="M696 808 L690 832 M680 829 L700 834"/>
        <path d="M768 770 L744 776 L752 808 A12 12 0 0 0 772 802 Z"/>
        <path d="M762 808 L768 832 M758 834 L778 829"/>
        <path d="M718 748 L721 754 L727 755 L722 759 L724 765 L718 762 L712 765 L714 759 L709 755 L715 754 Z"/>
        <path d="M742 744 L745 750 L751 751 L746 755 L748 761 L742 758 L736 761 L738 755 L733 751 L739 750 Z"/>
      </g>
    </g>

    <!-- badge: accountable -->
    <g class="badge badge-accountable">
      <circle class="badge-ring" cx="978" cy="797" r="87"/>
      <circle class="badge-core" cx="978" cy="797" r="73"/>
      <g class="icon">
        <circle cx="978" cy="797" r="22"/>
        <circle cx="978" cy="790" r="7"/>
        <path d="M966 812 A12 12 0 0 1 990 812"/>
        <line x1="978" y1="775" x2="978" y2="764"/><circle cx="978" cy="758" r="6"/>
        <line x1="978" y1="819" x2="978" y2="830"/><circle cx="978" cy="836" r="6"/>
        <line x1="956" y1="797" x2="945" y2="797"/><circle cx="939" cy="797" r="6"/>
        <line x1="1000" y1="797" x2="1011" y2="797"/><circle cx="1017" cy="797" r="6"/>
        <line x1="962" y1="781" x2="953" y2="772"/><circle cx="949" cy="768" r="6"/>
        <line x1="994" y1="781" x2="1003" y2="772"/><circle cx="1007" cy="768" r="6"/>
        <line x1="962" y1="813" x2="953" y2="822"/><circle cx="949" cy="826" r="6"/>
        <line x1="994" y1="813" x2="1003" y2="822"/><circle cx="1007" cy="826" r="6"/>
      </g>
    </g>

    <!-- behaviour labels -->
    <text class="behaviour-label" x="229"><tspan x="229" y="46">Proactive</tspan><tspan x="229" y="74">deliberate and</tspan><tspan x="229" y="102">team focussed</tspan></text>
    <text class="behaviour-label" x="478"><tspan x="478" y="78">Influence</tspan><tspan x="478" y="106">the agenda</tspan></text>
    <text class="behaviour-label" x="728"><tspan x="728" y="49">Collaborate and</tspan><tspan x="728" y="77">leverage the collective</tspan><tspan x="728" y="105">strength of the group</tspan></text>
    <text class="behaviour-label" x="978"><tspan x="978" y="74">Support Each</tspan><tspan x="978" y="102">Other</tspan></text>

    <text class="behaviour-label" x="222"><tspan x="222" y="921">Listen &amp; show</tspan><tspan x="222" y="949">you care</tspan></text>
    <text class="behaviour-label" x="475"><tspan x="475" y="921">Communicate</tspan><tspan x="475" y="949">openly</tspan></text>
    <text class="behaviour-label" x="729"><tspan x="729" y="921">Celebrate success</tspan><tspan x="729" y="949">&amp; have fun</tspan></text>
    <text class="behaviour-label" x="980" y="921">Be Accountable</text>
  </svg>
</main>
</body>
</html>
```